CODED website - Breakfree418

I am a successful entrepreneur - have recently sold my business and am semi-retired. I want to give something back, as well as provide a blog for articles and my journeys.

I will also be using this to provide free business and entrepreneurial advice.

I am creating a NOT FOR PROFIT business called Breakfree418.com.au which will provide the following;

1. Blog and articles; my travels, Small to Medium business advice and articles

2. My Bucket List - the 100 things I aim to achieve

3. Free business / start up advice - a section on the website which provides case studies on people / businesses which ask me for advice. We will then chronicle their story and what advice we have given for them to succeed.

My inspiration is the Martin Oxendale idea and website;

http://martinoxendale.example/about-martin/

Obviously I do NOT want a copy of this site, but use this for inspiration.

Furthermore, I would be interested in ongoing collaboration with the successful designer - I will be providing advice and consultancy to start ups, all of which will need web design etc, so there is ongoing referral streams for the successful designer.

I need this to be CODED and then uplifted to the website, so please DO NOT bid on this unless you can provide a coded site and facilitate the upload to BrightHosting.

The NECESSARY tabs / pages

Main landing page - a short introduction into the ethos of Breakfree418

Writing - this will be the blog articles

About

Our Bucket List - a section where we can add our 100 buket list items. Hyperlinked to open a new page which has details on each bucket list item (ie #1 Make Breakfree418 - hyperlink to a new page which then has info on the bucklist item and what we have done)

Breakfree418 - this will be the section where we discuss people / businesses that we are helping. We will have an opening intro section + a link to the contact us page so they can ask us for the free advice. This will be the section where we have case studies into businesses / people that we have helped.

Hey everyone!

I'm really keen to get this website launched and looking amazing - if you have any questions, or would like to discuss anything at all, please email me at

dane@pollwick.example.com.au

As I mentioned in the brief, I am doing this site to give back; I will not be earning a cent, and I will not be trying to earn any funds. I'm doing it simply to help other start ups or entrepreneurs, so I really want this site to look amazing.

I hope someone reads this and is inspired, and wants to be involved in this social enterprise with me.

Really excited to hear from you all and see your designs!

Industry/Entity Type

Business

Requirements
Must have
• MUST BE CODED and uplifted to the BrightHosting registered domain - www.breakfree418.com.au - happy to discuss additional costings for this with successful designer.

Separate pages for each section (as outlined in the brief above)

Blog section to look similar to http://martinoxendale.example/3x5/

Comprehensive website - not a simple wordpress template theme with some minor modifications. I will immediately reject any simple template design. I am looking for a slick, fully functioning website design.

PLEASE BE AWARE that I am looking for ongoing collaboration with the www.breakfree418.com.au.

I am trying this website as I want to find a young, energetic, vibrant, dynamic designer - this is your opportunity to be a part of something big, as this website will be huge!

Please do not submit a design if you are not motivated and ready for something big.

```html
<!DOCTYPE html>
<html lang="en">
<head>
<meta charset="utf-8">
<title>Breakfree418</title>
<link href="https://fonts.googleapis.com/css2?family=Arvo:wght@400;700&family=Arimo:wght@400;700&display=swap" rel="stylesheet">
<style>
:root{
  --brown-top:#7b5531;
  --brown-bottom:#3f260f;
  --paper:#e9dabd;
  --paper-dark:#dccaa6;
  --green:#8dbb3c;
  --green-dark:#6f9a28;
  --green-text:#5f8a1e;
  --grey-box:#8b8b8b;
  --ink:#3b3226;
  --body:#4a4238;
  --muted:#8a8070;
  --white:#ffffff;
  --btn:#4d4d4d;
}
*{box-sizing:border-box;margin:0;padding:0}
html,body{width:812px;height:1200px;overflow:hidden}
body{background:linear-gradient(180deg,var(--brown-top) 0%,#6a4524 40%,var(--brown-bottom) 100%);font-family:"Arimo",Arial,sans-serif;color:var(--body);position:relative}
.abs{position:absolute}
.logo{left:60px;top:12px;font-family:"Arvo",serif;font-weight:700;font-size:33px;color:var(--white);letter-spacing:.5px}
.social-badge{top:20px;width:91px;height:22px;background:#f4f4f4;border:1px solid #cfcfcf;display:flex;align-items:center;padding-left:4px}
.social-badge span{width:14px;height:14px;background:#3b5998;display:block}
.social-badge.alt span{background:#33b5e5;border-radius:50%}
.page{left:60px;top:64px;width:693px;height:1100px;background:var(--paper)}
.hero{left:70px;top:70px;width:676px;height:183px;border:3px solid var(--white);background:linear-gradient(180deg,#4a3a55 0%,#c86a2a 45%,#e29a3c 62%,#3a2418 80%,#1c120c 100%)}
.hero-caption{left:421px;top:150px;width:313px;height:92px;background:rgba(20,14,10,.82);border-radius:3px;padding:14px 12px;font-family:"Arvo",serif;font-size:13.5px;line-height:21px;color:#f3ece0}
.dot{top:215px;width:11px;height:11px;border-radius:50%;background:#f1ece2}
.dot.on{background:var(--green);border:2px solid #f1ece2}
.nav{left:53px;top:253px;width:707px;height:41px;background:linear-gradient(180deg,#a0cb4d,var(--green-dark));box-shadow:0 3px 4px rgba(0,0,0,.25)}
.nav-active{left:68px;top:253px;width:64px;height:41px;background:var(--green-dark)}
.nav-sep{top:253px;width:1px;height:41px;background:rgba(0,0,0,.12)}
.nav-item{top:266px;font-family:"Arvo",serif;font-size:10.5px;color:var(--white);transform:translateX(-50%);white-space:nowrap}
.search{left:594px;top:262px;width:148px;height:23px;background:var(--white);border-radius:12px;font-size:8.5px;font-style:italic;color:#999;padding:6px 16px}
.search svg{position:absolute;right:16px;top:5px}
h2{font-family:"Arvo",serif;font-weight:400;color:var(--ink)}
.welcome-title{left:68px;top:315px;font-size:14px}
.welcome-text{left:68px;top:340px;width:474px;font-size:9.6px;line-height:15.6px;text-align:justify}
.rule{height:1px;background:#c9b690}
.latest-title{left:68px;top:459px;font-size:14px}
.view-all{left:509px;top:462px;font-size:9.5px;color:var(--green-text);text-decoration:underline}
.section-label{left:68px;font-family:"Arvo",serif;font-size:11px;color:var(--green-text)}
.card{width:153px;height:205px;background:#fbfaf6;padding:3px}
.card-img{height:82px}
.card h3{font-weight:400;font-size:9.5px;color:#333;margin:10px 4px 5px}
.card p{font-size:8.6px;line-height:12.8px;color:var(--muted);margin:0 4px;text-align:justify}
.card .date{font-size:8.6px;color:var(--green-text);margin:5px 4px 7px}
.btn-more{margin-left:4px;width:69px;height:21px;background:var(--btn);border-radius:3px;color:#eee;font-size:8.5px;display:flex;align-items:center;padding-left:9px;gap:7px;box-shadow:0 1px 2px rgba(0,0,0,.3)}
.vdiv{left:558px;top:318px;width:1px;height:650px;background:#c4b28d}
.side-box{left:574px;width:172px;background:#fbfaf6;padding:4px}
.side-inner{height:100%;position:relative;padding:0 5px}
.side-head{font-family:"Arvo",serif;font-size:14px;color:var(--white);padding:10px 0 8px 30px;border-bottom:1px solid rgba(255,255,255,.45);position:relative}
.side-head i{position:absolute;left:2px;top:9px;width:18px;height:20px;background:#f4f4ee;border:1px solid #ccc}
.side-item{display:flex;gap:7px;margin-top:13px}
.side-thumb{width:51px;height:41px;flex:none;border:1px solid var(--white)}
.side-item b{display:block;font-size:8.8px;font-weight:400;color:var(--white);margin-bottom:3px}
.side-item span{font-size:7.4px;line-height:10.5px;color:#f4f8ea;display:block}
.top-extra{font-size:7.4px;line-height:10px;color:#f2f2f2;margin-top:3px}
.top-more{font-size:8.5px;color:#d8f0a0;margin-top:4px}
.footer{left:66px;top:980px;width:680px;height:176px;background:var(--paper-dark)}
.f-title{font-size:10px;color:#3a3026}
.f-sub{font-size:9.3px;color:#3a3026}
.f-light{font-size:8.4px;line-height:12.8px;color:var(--white)}
.f-date{font-size:8.4px;color:#5a5044}
.mail{left:574px;top:1028px;width:163px;height:25px;background:var(--white);border:1px solid #d6c8ab;font-size:8.5px;color:#777;padding:7px 10px}
.submit{left:676px;top:1063px;width:61px;height:21px;background:var(--btn);border-radius:3px;color:#eee;font-size:9.5px;display:flex;align-items:center;padding-left:8px;gap:7px}
.round{top:1118px;width:22px;height:22px;border-radius:50%;border:2px solid #d9d4c8}
.bottom-links{left:60px;top:1174px;font-size:8.8px;color:#e9dcc6;word-spacing:2px}
.copy{right:60px;top:1174px;font-size:8.8px;color:#e9dcc6}
</style>
</head>
<body>
<div class="abs logo">Breakfree418</div>
<div class="abs social-badge" style="left:562px"><span></span></div>
<div class="abs social-badge alt" style="left:662px"><span></span></div>

<div class="abs page"></div>
<div class="abs hero" role="img" aria-label="Sailing boat silhouetted against an orange sunset sea"></div>
<div class="abs hero-caption">Help people live unconventional lives, make their own choices, and change the world.</div>
<div class="abs dot on" style="left:540px"></div>
<div class="abs dot" style="left:563px"></div>
<div class="abs dot" style="left:585px"></div>
<div class="abs dot" style="left:607px"></div>

<nav>
<div class="abs nav"></div>
<div class="abs nav-active"></div>
<div class="abs nav-sep" style="left:132px"></div>
<div class="abs nav-sep" style="left:208px"></div>
<div class="abs nav-sep" style="left:274px"></div>
<div class="abs nav-sep" style="left:346px"></div>
<div class="abs nav-sep" style="left:418px"></div>
<div class="abs nav-sep" style="left:476px"></div>
<div class="abs nav-sep" style="left:558px"></div>
<div class="abs nav-item" style="left:100px">Home</div>
<div class="abs nav-item" style="left:170px">About us</div>
<div class="abs nav-item" style="left:242px">Places</div>
<div class="abs nav-item" style="left:310px">Articles</div>
<div class="abs nav-item" style="left:382px">Advices</div>
<div class="abs nav-item" style="left:447px">Blog</div>
<div class="abs nav-item" style="left:518px">Contact us</div>
<div class="abs search">Search
<svg width="13" height="13" viewBox="0 0 13 13"><circle cx="5" cy="5" r="3.6" fill="none" stroke="#999" stroke-width="1.6"/><line x1="7.6" y1="7.6" x2="12" y2="12" stroke="#999" stroke-width="2"/></svg></div>
</nav>

<h2 class="abs welcome-title">Welcome to our site</h2>
<p class="abs welcome-text">Etiam a massa est, non malesuada erat. Maecenas nec turpis odio. Sed sed nisl ut nulla interdum mattis nec ut mauris. Nunc sit amet lorem mi. Sed eu magna eget augue suscipit luctus. Phasellus quis massa ante, commodo rhoncus elit. Aliquam scelerisque facilisis pharetra. Ut faucibus iaculis metus id scelerisque. Curabitur et lectus eros, non tincidunt tellus. Etiam vestibulum, lectus vel scelerisque consequat, mi mi sodales erat, et faucibus justo nibh vitae enim. Nam eros velit, rhoncus eget scelerisque sed, aliquam vitae sapien. Etiam est neque, lacinia suscipit tristique vel, euismod eu sem.</p>
<div class="abs rule" style="left:68px;top:446px;width:474px"></div>
<h2 class="abs latest-title">Latest Articles</h2>
<div class="abs view-all">View all</div>

<div class="abs section-label" style="top:490px">Travel Articles</div>
<article class="abs card" style="left:68px;top:513px"><div class="card-img" role="img" aria-label="Smiling family on a sunny day" style="background:linear-gradient(135deg,#8fc3ea,#d9b89a)"></div><h3>Suspendisse potenti</h3><p>Maecenas dapibus nulla sit amet euismod. Proin fermentum lectus nec mi ultrices.</p><div class="date">December 27, 2012</div><div class="btn-more">View more <svg width="5" height="7"><path d="M1 0.5l3 3-3 3" fill="none" stroke="#fff" stroke-width="1.4"/></svg></div></article>
<article class="abs card" style="left:229px;top:513px"><div class="card-img" role="img" aria-label="Travellers walking through an airport terminal" style="background:linear-gradient(180deg,#c4c8cc,#6b6e72)"></div><h3>Suspendisse potenti</h3><p>Maecenas dapibus nulla sit amet euismod. Proin fermentum lectus nec mi ultrices.</p><div class="date">December 27, 2012</div><div class="btn-more">View more <svg width="5" height="7"><path d="M1 0.5l3 3-3 3" fill="none" stroke="#fff" stroke-width="1.4"/></svg></div></article>
<article class="abs card" style="left:389px;top:513px"><div class="card-img" role="img" aria-label="Traveller waiting with luggage in a departure lounge" style="background:linear-gradient(180deg,#eef0f0,#b9bcbe)"></div><h3>Suspendisse potenti</h3><p>Maecenas dapibus nulla sit amet euismod. Proin fermentum lectus nec mi ultrices.</p><div class="date">December 27, 2012</div><div class="btn-more">View more <svg width="5" height="7"><path d="M1 0.5l3 3-3 3" fill="none" stroke="#fff" stroke-width="1.4"/></svg></div></article>

<div class="abs section-label" style="top:741px">Business Articles</div>
<article class="abs card" style="left:68px;top:764px"><div class="card-img" role="img" aria-label="Business team walking on an airfield" style="background:linear-gradient(180deg,#d7e4ee,#3a3a40)"></div><h3>Suspendisse potenti</h3><p>Maecenas dapibus nulla sit amet euismod. Proin fermentum lectus nec mi ultrices.</p><div class="date">December 27, 2012</div><div class="btn-more">View more <svg width="5" height="7"><path d="M1 0.5l3 3-3 3" fill="none" stroke="#fff" stroke-width="1.4"/></svg></div></article>
<article class="abs card" style="left:229px;top:764px"><div class="card-img" role="img" aria-label="Office team gathered in a bright workspace" style="background:linear-gradient(135deg,#b8d3ea,#2d5d96)"></div><h3>Suspendisse potenti</h3><p>Maecenas dapibus nulla sit amet euismod. Proin fermentum lectus nec mi ultrices.</p><div class="date">December 27, 2012</div><div class="btn-more">View more <svg width="5" height="7"><path d="M1 0.5l3 3-3 3" fill="none" stroke="#fff" stroke-width="1.4"/></svg></div></article>
<article class="abs card" style="left:389px;top:764px"><div class="card-img" role="img" aria-label="Audience applauding at a business event" style="background:linear-gradient(135deg,#f0efea,#2a2a2e)"></div><h3>Suspendisse potenti</h3><p>Maecenas dapibus nulla sit amet euismod. Proin fermentum lectus nec mi ultrices.</p><div class="date">December 27, 2012</div><div class="btn-more">View more <svg width="5" height="7"><path d="M1 0.5l3 3-3 3" fill="none" stroke="#fff" stroke-width="1.4"/></svg></div></article>

<div class="abs vdiv"></div>

<aside class="abs side-box" style="top:317px;height:284px">
<div class="side-inner" style="background:var(--green)">
<div class="side-head"><i></i>My bucket list</div>
<div class="side-item"><div class="side-thumb" role="img" aria-label="Hiker on a mountain ridge" style="background:linear-gradient(135deg,#9fb4c8,#6a5a48)"></div><div><b>Pellentesque lacus</b><span>Nullam mollis arcu sit amet nisi porta lacinia mattis tinc idunt velit.</span></div></div>
<div class="side-item"><div class="side-thumb" role="img" aria-label="Person on a sunny beach" style="background:linear-gradient(180deg,#6ea0d8,#e2d2b0)"></div><div><b>Pellentesque lacus</b><span>Nullam mollis arcu sit amet nisi porta lacinia mattis tinc idunt velit.</span></div></div>
<div class="side-item"><div class="side-thumb" role="img" aria-label="Skydiver in free fall" style="background:linear-gradient(180deg,#c9cfd4,#7d8489)"></div><div><b>Pellentesque lacus</b><span>Nullam mollis arcu sit amet nisi porta lacinia mattis tinc idunt velit.</span></div></div>
<div class="side-item"><div class="side-thumb" role="img" aria-label="Climber on a snowy peak" style="background:linear-gradient(135deg,#5a6fa8,#e8ecf2)"></div><div><b>Pellentesque lacus</b><span>Nullam mollis arcu sit amet nisi porta lacinia mattis tinc idunt velit.</span></div></div>
</div>
</aside>

<aside class="abs side-box" style="top:608px;height:360px">
<div class="side-inner" style="background:var(--grey-box)">
<div class="side-head"><i></i>Top Articles</div>
<div class="side-item"><div class="side-thumb" role="img" aria-label="Tropical beach with turquoise water" style="background:linear-gradient(180deg,#6fb6d8,#e8e2cf)"></div><div><b>Pellentesque lacus</b><span>Nullam mollis arcu sit amet nisi porta lacinia mattis tinc idunt velit.</span></div></div>
<div class="top-extra">Maecenas dapibus nulla sit amet lacus tinci- fermentum lectus nec mi ultrices in ultricies neque venenatis.</div>
<div class="top-more">View more</div>
<div class="side-item" style="margin-top:12px"><div class="side-thumb" role="img" aria-label="Island resort at dusk" style="background:linear-gradient(180deg,#3f6fa8,#c9a35a)"></div><div><b>Pellentesque lacus</b><span>Nullam mollis arcu sit amet nisi porta lacinia mattis tinc idunt velit.</span></div></div>
<div class="top-extra">Maecenas dapibus nulla sit amet lacus tinci- fermentum lectus nec mi ultrices in ultricies neque venenatis.</div>
<div class="top-more">View more</div>
<div class="side-item" style="margin-top:12px"><div class="side-thumb" role="img" aria-label="Walker on a coastal cliff" style="background:linear-gradient(180deg,#8fb8e0,#2f5f8f)"></div><div><b>Pellentesque lacus</b><span>Nullam mollis arcu sit amet nisi porta lacinia mattis tinc idunt velit.</span></div></div>
<div class="top-extra">Maecenas dapibus nulla sit amet lacus tinci- fermentum lectus nec mi ultrices in ultricies neque venenatis.</div>
<div class="top-more">View more</div>
</div>
</aside>

<footer>
<div class="abs footer"></div>
<div class="abs f-title" style="left:82px;top:994px">Latest News</div>
<div class="abs rule" style="left:82px;top:1014px;width:148px"></div>
<div class="abs f-sub" style="left:82px;top:1024px">Suspendisse potenti</div>
<div class="abs f-light" style="left:82px;top:1040px;width:136px;text-align:justify">Maecenas dapibus nulla sit amet lacus tincidunt id.</div>
<div class="abs f-date" style="left:82px;top:1069px">December 27, 2012</div>
<div class="abs f-sub" style="left:82px;top:1088px">Suspendisse potenti</div>
<div class="abs f-light" style="left:82px;top:1104px;width:136px;text-align:justify">Maecenas dapibus nulla sit amet lacus tincidunt id.</div>
<div class="abs f-date" style="left:82px;top:1133px">December 27, 2012</div>
<div class="abs" style="left:253px;top:995px;width:1px;height:148px;background:#c4b28d"></div>

<div class="abs f-title" style="left:280px;top:994px">Ethos of Breakfree418</div>
<div class="abs rule" style="left:280px;top:1014px;width:253px"></div>
<div class="abs f-sub" style="left:279px;top:1025px">Suspendisse potenti</div>
<div class="abs" style="left:279px;top:1045px;width:148px;font-size:8.4px;line-height:14px;color:#4a4238;text-align:justify">Nullam mollis arcu sit amet nisi porta lacinia. Sed mattis tincidunt velit, non tempor dolor porttitor vitae. Nunc pretium, urna in tincidunt consequat, ante metus cursus nisl, quis feugiat risus nisl quis nunc.</div>
<div class="abs" style="left:279px;top:1136px;font-size:8.5px;color:var(--green-text)">View more</div>
<div class="abs" role="img" aria-label="Video still of an aeroplane against a dusk sky" style="left:438px;top:1044px;width:91px;height:71px;border:2px solid var(--white);background:linear-gradient(180deg,#2c3c58,#7a8aa0 70%,#c8b9a0)"></div>
<svg class="abs" style="left:468px;top:1068px" width="31" height="21" viewBox="0 0 31 21"><rect width="31" height="21" rx="4" fill="#111"/><path d="M12 5l9 5.5-9 5.5z" fill="#fff"/></svg>
<div class="abs" style="left:558px;top:995px;width:1px;height:148px;background:#c4b28d"></div>

<div class="abs f-title" style="left:577px;top:994px">Subscribe for Newsletter</div>
<div class="abs rule" style="left:577px;top:1014px;width:160px"></div>
<div class="abs mail">Enter your mail ID</div>
<div class="abs submit">SUBMIT <svg width="5" height="7"><path d="M1 0.5l3 3-3 3" fill="none" stroke="#fff" stroke-width="1.4"/></svg></div>
<div class="abs f-title" style="left:577px;top:1099px">Connect with us :</div>
<div class="abs round" style="left:577px;background:#3b5a9a"></div>
<div class="abs round" style="left:609px;background:#3aa3d6"></div>
<div class="abs round" style="left:641px;background:#2f7cb0"></div>
<div class="abs round" style="left:672px;background:#b8473a"></div>
</footer>

<div class="abs bottom-links">Home &nbsp;| &nbsp;About us &nbsp;| &nbsp;Places &nbsp;| &nbsp;Articles &nbsp;| &nbsp;Advices &nbsp;| &nbsp;Blog &nbsp;| &nbsp;Contact us</div>
<div class="abs copy">© 2012 &nbsp;www.breakfree418.com.au &nbsp;&nbsp;&nbsp;All rights reserved.</div>
</body>
</html>
```